Market Research firm needs updated business cards with new logo

We need the logo to be included somewhere on the card (attached). We would also like the phrases "Independent, Objective, Comprehensive" and "Research You Can Trust" somewhere on the card. Front or back. Our colors are hex codes 6075a7, e48d25 and 5a5b5b. Though you are certainly not limited to those shades, whatever you produce should coordinate with them. I have also attached our favicon. Feel free to use it in your design, but please do not use it to replace the full logo.

Contact Information for Business Card

see project description

Font styles to use
Other font styles liked:
• Open Sans

Requirements
Must have
• the logo
• We use Open Sans font

```html
<!DOCTYPE html>
<html lang="en">
<head>
<meta charset="utf-8">
<title>Northvale Research – Business Card</title>
<link rel="stylesheet" href="https://fonts.googleapis.com/css2?family=Open+Sans:wght@400;600&display=swap">
<style>
  :root {
    --brand-blue: #6075a7;
    --brand-orange: #e48d25;
    --card-grey: #5a5b5b;
    --ink-white: #ffffff;
    --backdrop-dark: #000000;
    --backdrop-teal: #012c2c;
  }
  * { margin: 0; padding: 0; box-sizing: border-box; }
  html, body { width: 1200px; height: 1200px; overflow: hidden; }
  body {
    background: linear-gradient(90deg, var(--backdrop-dark) 0%, #00191a 45%, var(--backdrop-teal) 100%);
    font-family: "Open Sans", Arial, sans-serif;
    position: relative;
  }
  .card {
    position: absolute;
    left: 180px;
    width: 840px;
    height: 480px;
    border-radius: 24px;
    background: var(--card-grey);
    overflow: hidden;
  }
  .card--front { top: 104px; }
  .card--back { top: 616px; }

  .wordmark {
    position: absolute;
    white-space: nowrap;
    font-weight: 600;
    line-height: 1;
  }
  .card--front .wordmark {
    left: 0; right: 0; top: 40px;
    text-align: center;
    font-size: 62px;
    color: var(--brand-orange);
  }
  .card--back .wordmark {
    left: 0; right: 0; top: 170px;
    text-align: center;
    font-size: 76px;
    color: var(--ink-white);
  }

  .brand-disc {
    position: absolute;
    left: 60px; top: 204px;
    width: 240px; height: 240px;
    border-radius: 50%;
    background: var(--brand-blue);
  }

  .contact-list { list-style: none; }
  .contact-item {
    position: absolute;
    right: 60px;
    display: flex;
    align-items: center;
    gap: 40px;
    color: var(--ink-white);
  }
  .contact-item .value { line-height: 1; }
  .contact-item--phone { top: 212px; font-size: 36px; }
  .contact-item--fax { top: 290px; font-size: 36px; }
  .contact-item--email { top: 355px; font-size: 32px; }
  .contact-item--web { top: 426px; font-size: 32px; }
  .contact-icon { width: 48px; height: 48px; flex: none; }

  .tagline {
    position: absolute;
    top: 278px;
    font-size: 22px;
    color: var(--ink-white);
    white-space: nowrap;
  }
  .tagline--independent { left: 28px; }
  .tagline--objective { left: 220px; }
  .tagline--comprehensive { left: 340px; }
  .tagline--trust { left: 548px; }
</style>
</head>
<body>
  <section class="card card--front">
    <div class="wordmark">Northvale Research</div>
    <div class="brand-disc" role="img" aria-label="Brand mark area"></div>
    <ul class="contact-list">
      <li class="contact-item contact-item--phone">
        <span class="value">455 555 555</span>
        <svg class="contact-icon" viewBox="0 0 48 48" aria-hidden="true">
          <circle cx="24" cy="24" r="23" fill="var(--brand-orange)"/>
          <path d="M16 13c2-1 3 0 4 2l2 4c0 1 0 2-1 3l-1 1c1 3 3 5 6 6l1-1c1-1 2-1 3-1l4 2c2 1 3 2 2 4l-1 2c-1 1-3 2-5 1-8-2-14-8-16-16-1-2 0-4 1-5z" fill="var(--card-grey)"/>
        </svg>
      </li>
      <li class="contact-item contact-item--fax">
        <span class="value">455 676 543</span>
        <svg class="contact-icon" viewBox="0 0 48 48" aria-hidden="true" fill="none" stroke="var(--brand-orange)" stroke-width="2.5">
          <rect x="13" y="2" width="22" height="22"/>
          <line x1="17" y1="9" x2="31" y2="9"/>
          <line x1="17" y1="14" x2="31" y2="14"/>
          <line x1="17" y1="19" x2="31" y2="19"/>
          <rect x="2" y="24" width="44" height="22" rx="3"/>
          <path d="M12 40c0-7 24-7 24 0" stroke-width="4"/>
        </svg>
      </li>
      <li class="contact-item contact-item--email">
        <span class="value">youremail@example.com</span>
        <svg class="contact-icon" viewBox="0 0 48 48" aria-hidden="true" fill="none" stroke="var(--brand-orange)" stroke-width="3">
          <rect x="3" y="8" width="42" height="32" rx="3"/>
          <path d="M3 10l21 18 21-18M3 38l15-14M45 38l-15-14"/>
        </svg>
      </li>
      <li class="contact-item contact-item--web">
        <span class="value">www.yourweb.com</span>
        <svg class="contact-icon" viewBox="0 0 48 48" aria-hidden="true" fill="none" stroke="var(--brand-orange)" stroke-width="3">
          <circle cx="24" cy="24" r="21"/>
          <ellipse cx="24" cy="24" rx="9" ry="21"/>
          <line x1="3" y1="24" x2="45" y2="24"/>
          <line x1="24" y1="3" x2="24" y2="45"/>
        </svg>
      </li>
    </ul>
  </section>

  <section class="card card--back">
    <div class="wordmark">Northvale Research</div>
    <p class="tagline tagline--independent">Independent</p>
    <p class="tagline tagline--objective">Objective</p>
    <p class="tagline tagline--comprehensive">Comprehensive</p>
    <p class="tagline tagline--trust">Research You Can Trust</p>
  </section>
</body>
</html>
```